Pre-workout label and Super Greens label for Brightmoor Nutrition Supplements

I need a label design for Club Brightmoor's 2 supplements. The first is a Pre-workout. The Pre-workout label needs to be 11.25 x 2.5 inches. This label will go on a black container. The second is a Super-Green. The Super-Green label should be 11.25 x 4.25 inches and will go on a white container. We have been selling these for a few years but the current labels are a little meh. I'd like something trendier and bolder. Must keep the Club Brightmoor branding. All the nurtition data must appear . I attached the current designs so you can know the flavors, nutrtional data etc. Thank you!
Updates

I can upload the Club Brightmoor logo! If anyone can tell me how to do that.

```html
<!DOCTYPE html>
<html lang="en">
<head>
<meta charset="utf-8">
<title>Brightmoor Nutrition Pre-Workout Label</title>
<link href="https://fonts.googleapis.com/css2?family=Russo+One&family=Montserrat:wght@400;600;700&display=swap" rel="stylesheet">
<style>
:root{
  --page:#f4f4f4;
  --label-red:#e01f2a;
  --pattern-red:#c8141e;
  --panel-red:#b40f18;
  --ink-light:#ffffff;
  --ink-soft:#f2dede;
  --ink-dark:#1a1a1a;
  --pill-text:#d0141f;
}
*{margin:0;padding:0;box-sizing:border-box}
html,body{width:800px;height:1200px;overflow:hidden;background:var(--page)}
body{position:relative;font-family:"Montserrat",sans-serif;color:var(--ink-light)}
.label{position:absolute;left:20px;top:510px;width:760px;height:180px;overflow:hidden}
.label-pattern{position:absolute;inset:0;background:radial-gradient(circle at 50% 50%,var(--label-red) 0%,var(--pattern-red) 100%)}
.side-panel{position:absolute;left:18px;top:12px;width:203px;height:156px;background:var(--panel-red);text-align:center;padding:0 14px}
.side-title{font-family:"Russo One",sans-serif;font-size:15px;margin-top:9px;letter-spacing:.3px}
.directions{font-size:5px;line-height:1.35;margin-top:5px;color:var(--ink-soft)}
.warning{font-size:3.6px;line-height:1.38;margin-top:5px;color:var(--ink-soft)}
.warning b{color:var(--ink-light)}
.side-rule{height:.6px;background:var(--ink-light);margin:6px 4px 0}
.fda-box{width:84px;margin:5px auto 0;background:var(--ink-light);color:var(--ink-dark);font-size:3.2px;line-height:1.3;padding:2px}
.front{position:absolute;left:260px;top:0;width:240px;height:180px;text-align:center}
.brand-mark{display:flex;align-items:center;justify-content:center;gap:3px;margin-top:11px;font-family:"Russo One",sans-serif;font-size:7px;letter-spacing:.5px}
.brand-mark i{display:block;width:6px;height:6px;background:var(--ink-light)}
.brand-line{font-family:"Russo One",sans-serif;font-size:9px;letter-spacing:1.6px;margin-top:9px}
.product-name{font-family:"Russo One",sans-serif;font-size:27px;line-height:1;margin-top:3px;letter-spacing:.5px}
.flavor-pill{display:inline-block;background:var(--ink-light);color:var(--pill-text);font-family:"Russo One",sans-serif;font-size:6.5px;letter-spacing:.8px;padding:1.5px 6px;border-radius:5px;margin-top:5px}
.benefits{display:flex;justify-content:center;gap:18px;margin-top:5px}
.benefit{width:36px;font-family:"Russo One",sans-serif;font-size:4.6px;line-height:1.25}
.benefit-icon{display:block;width:18px;height:18px;margin:0 auto 3px;border-radius:4px;background:var(--ink-soft);opacity:.85}
.front-footer{position:absolute;left:0;right:0;top:159px;display:flex;justify-content:space-between;padding:0 14px 0 20px;font-size:5.2px;font-weight:700;letter-spacing:.3px}
.facts-area{position:absolute;left:545px;top:16px;width:192px}
.facts{background:var(--ink-light);color:var(--ink-dark);padding:3px 4px 3px;border:.5px solid var(--ink-dark)}
.facts-title{font-weight:700;font-size:7px;line-height:1}
.serving{font-size:3.6px;line-height:1.3;margin-top:1px}
.facts table{width:100%;border-collapse:collapse;font-size:3.7px;margin-top:1px;border-top:2px solid var(--ink-dark)}
.facts th{font-weight:700;text-align:left;padding:.8px 0;border-bottom:1px solid var(--ink-dark)}
.facts td{padding:.9px 0;border-bottom:.4px solid var(--ink-dark);line-height:1.15}
.facts .amt{width:70px}
.facts .dv{width:18px;text-align:right}
.facts tr:last-child td{border-bottom:2px solid var(--ink-dark)}
.facts-note{font-size:3px;margin-top:1px}
.other-ingredients{font-size:4.2px;line-height:1.4;margin-top:8px;color:var(--ink-soft)}
.formulator{font-size:4.2px;margin-top:6px;color:var(--ink-soft)}
</style>
</head>
<body>
<section class="label">
  <div class="label-pattern" role="img" aria-label="Organic red coral-like decorative pattern across the whole label"></div>

  <aside class="side-panel">
    <h2 class="side-title">PRE-WORKOUT</h2>
    <p class="directions">Directions: Use on training days only. Mix 1 scoop with 6-8 oz of cold water 15-30 minutes prior to training.</p>
    <p class="warning"><b>Warning:</b> Not intended for use by persons under age 18. Do not exceed recommended dose. Do not consume synephrine or caffeine from other sources, including but not limited to: coffee, tea, soda, and other dietary supplements or medications containing phenylephrine or caffeine. Contains caffeine. Use in a 12 week on, 2 week off pattern. Consult your physician prior to use if you are pregnant or nursing, or if you are taking medication, including but not limited to: MAOI inhibitors, antidepressants, aspirin, non-steroidal, anti-inflammatory drugs or products containing phenylephrine, ephedrine, pseudoephedrine, or other stimulants. Consult your physician prior to use if you have a medical condition, including but not limited to: heart, liver, kidney, or thyroid disease, cardiac arrhythmia, recurrent headaches, enlarged prostate or glaucoma. Discontinue use 2 weeks prior to surgery or if you experience rapid heartbeat, dizziness, severe headaches, or shortness of breath. This product DOES NOT contain ingredients banned by certain sports organizations.</p>
    <div class="side-rule"></div>
    <p class="fda-box">*These statements have not been evaluated by the Food and Drug Administration. This product is not intended to diagnose, treat, cure or prevent any disease.</p>
  </aside>

  <div class="front">
    <div class="brand-mark"><i></i>BRIGHTMOOR</div>
    <div class="brand-line">BRIGHTMOOR NUTRITION</div>
    <h1 class="product-name">PRE-WORKOUT</h1>
    <div class="flavor-pill">WATERMELON SUGAR</div>
    <div class="benefits">
      <div class="benefit"><span class="benefit-icon" role="img" aria-label="Energy icon"></span>ENERGY*<br>(CAFFEINE)</div>
      <div class="benefit"><span class="benefit-icon" role="img" aria-label="Performance icon"></span>PERFORMANCE*<br>(BETA-ALANINE)</div>
      <div class="benefit"><span class="benefit-icon" role="img" aria-label="Strength icon"></span>STRENGTH*<br>(CREATINE)</div>
    </div>
    <div class="front-footer"><span>DIETARY SUPPLEMENT</span><span>30 SERVINGS 240g (8.5OZ)</span></div>
  </div>

  <div class="facts-area">
    <div class="facts">
      <div class="facts-title">Supplement Facts</div>
      <div class="serving">Serving Size: 1 Scoop (8 g)<br>Servings per Container: 30</div>
      <table>
        <tr><th></th><th class="amt">Amount per Serving</th><th class="dv">%DV</th></tr>
        <tr><td>Vitamin C (Ascorbic Acid)</td><td class="amt">250mg</td><td class="dv">278%</td></tr>
        <tr><td>Vitamin B6 (as Pyridoxal-5'-Phosphate)</td><td class="amt">0.035 mg</td><td class="dv">2%</td></tr>
        <tr><td>Folate</td><td class="amt">250 mcg DFE (150 mcg Folic Acid)</td><td class="dv">63%</td></tr>
        <tr><td>Vitamin B12 (as Methylcobalamin)</td><td class="amt">20 mcg</td><td class="dv">833%</td></tr>
        <tr><td>Calcium (as Calcium Silicate)</td><td class="amt">18.30 mg</td><td class="dv">1%</td></tr>
        <tr><td>Beta-Alanine</td><td class="amt">1.5 g</td><td class="dv">†</td></tr>
        <tr><td>Creatine Monohydrate</td><td class="amt">1 g</td><td class="dv">†</td></tr>
        <tr><td>L-Arginine Alpha-Ketoglutarate</td><td class="amt">1 g</td><td class="dv">†</td></tr>
        <tr><td>L-Citrulline Malate</td><td class="amt">1 g</td><td class="dv">†</td></tr>
        <tr><td>N-Acetyl L-Tyrosine</td><td class="amt">500 mg</td><td class="dv">†</td></tr>
        <tr><td>Caffeine Anhydrous</td><td class="amt">250 mg</td><td class="dv">†</td></tr>
        <tr><td>Synephrine HCl</td><td class="amt">30 mg</td><td class="dv">†</td></tr>
      </table>
      <div class="facts-note">† Daily Value (DV) not established</div>
    </div>
    <p class="other-ingredients">Other Ingredients: Citric Acid, Pineapple Fruit Juice Powder, Silicon Dioxide, Natural and Artificial Flavors, Acesulfame Potassium, Sucralose, and FD&amp;C Red #40.</p>
    <p class="formulator">Formulated by: Club Brightmoor, 482 County Rd 9 Harlow, WY 82990 (307) 555-0148</p>
  </div>
</section>
</body>
</html>
```